Website design for an Italian restaurant in Amsterdam

I need a design for a client of mine. It is for Teatro Lucerna, an Italian restaurant in Amsterdam.
We are going for a clean, modern look but we also need to realise an authentic feel.
The restaurant is located in an old movie theatre, that is where the name Teatro Lucerna comes from.
Industry/Entity Type
Italian Restaurant
Number of Pages Required
1 page
Font styles to use
Sans Serif
Colors
Designer to choose colors to be used in the design.

```html
<!DOCTYPE html>
<html lang="en">
<head>
<meta charset="utf-8">
<title>Teatro Lucerna – Ristorante Italiano</title>
<link href="https://fonts.googleapis.com/css2?family=Cinzel:wght@400;700&family=Great+Vibes&family=Roboto:wght@400;500;700&display=swap" rel="stylesheet">
<style>
  :root{
    --white:#ffffff;
    --page:#f6f5f3;
    --ink:#3a3a3a;
    --muted:#6f6f6f;
    --nav-active:#f1f1f1;
    --tan:#a88c67;
    --tan-dark:#8f7654;
    --tan-field:#b9a07e;
    --gold:#e4b31b;
    --wine:#b52a4c;
    --hero-dark:#2c2116;
    --hero-mid:#6e5330;
    --hero-warm:#b48a45;
  }
  *{box-sizing:border-box;margin:0;padding:0}
  html,body{width:1200px;height:897px;overflow:hidden;background:var(--page)}
  body{font-family:'Roboto',sans-serif;color:var(--ink);position:relative}

  .site-header{position:absolute;top:0;left:0;width:1200px;height:89px;background:var(--white);z-index:3}
  .brand-badge{position:absolute;left:112px;top:0;width:294px;height:136px}
  .brand-badge svg{position:absolute;inset:0}
  .brand-name{position:absolute;left:0;right:0;top:50px;text-align:center;font-family:'Cinzel',serif;font-weight:700;font-size:21px;color:var(--ink);letter-spacing:.5px}
  .brand-dot{display:block;width:14px;height:14px;border-radius:50%;background:var(--wine);margin:0 auto 8px;position:absolute;left:140px;top:-24px}
  .brand-tag{position:absolute;left:0;right:0;top:78px;text-align:center;font-size:9px;color:var(--wine);letter-spacing:1px}

  .main-nav{position:absolute;left:444px;top:0;height:89px;display:flex}
  .main-nav a{display:flex;align-items:center;padding:0 20px;height:89px;font-size:10.5px;font-weight:500;color:var(--ink);text-decoration:none;letter-spacing:.3px}
  .main-nav a.is-active{background:var(--nav-active)}
  .contact-block{position:absolute;left:912px;top:22px;text-align:right;width:152px}
  .contact-hours{font-size:9px;color:var(--muted);display:flex;justify-content:flex-end;align-items:center;gap:4px}
  .contact-phone{font-size:17px;color:var(--ink);margin-top:4px}

  .hero{position:absolute;top:89px;left:0;width:1200px;height:499px;
    background:radial-gradient(ellipse at 55% 35%,var(--hero-warm) 0%,var(--hero-mid) 45%,var(--hero-dark) 100%)}
  .hero-content{position:absolute;left:0;right:0;top:148px;text-align:center;color:var(--white)}
  .hero-rule{width:242px;height:1.5px;background:var(--white);margin:0 auto;opacity:.9}
  .hero-script{font-family:'Great Vibes',cursive;font-size:62px;line-height:1;margin-top:28px}
  .hero-title{font-family:'Cinzel',serif;font-size:50px;line-height:1;margin-top:14px;letter-spacing:1px}
  .hero-lead{font-size:14px;line-height:17px;margin:18px auto 0;width:300px}
  .hero-content .hero-rule.bottom{margin-top:30px}

  .reserve-bar{position:absolute;top:588px;left:0;width:1200px;height:71px;background:var(--tan);color:var(--white)}
  .reserve-heading{position:absolute;left:180px;top:14px;line-height:1}
  .reserve-heading strong{display:block;font-size:20px;font-weight:700}
  .reserve-heading span{display:block;font-size:15px;margin-top:4px}
  .reserve-divider{position:absolute;left:290px;top:0}
  .field-label{position:absolute;top:27px;font-size:15px}
  .field{position:absolute;top:21px;height:31px;background:var(--tan-field);font-size:13px;color:#ede3d4;display:flex;align-items:center;justify-content:space-between;padding:0 10px 0 20px}
  .reserve-btn{position:absolute;left:920px;top:21px;width:99px;height:33px;background:var(--gold);color:var(--white);font-size:12px;font-weight:700;display:flex;align-items:center;justify-content:center}

  .specials{position:absolute;top:659px;left:0;width:1200px;height:238px;background:var(--white)}
  .specials-title{text-align:center;font-family:'Cinzel',serif;font-size:17px;color:var(--ink);margin-top:26px}
  .specials-rule{width:80px;height:1px;background:var(--tan);margin:10px auto 0}
  .dish-row{display:flex;justify-content:center;gap:22px;margin-top:26px}
  .dish{display:flex;width:262px;height:118px}
  .dish-photo{width:130px;height:118px;background:linear-gradient(135deg,#c9853c,#8e3f23 60%,#5a6b2c)}
  .dish-text{flex:1;padding:26px 10px 0;text-align:center}
  .dish-text h3{font-size:11px;font-weight:500;letter-spacing:.5px;color:var(--ink)}
  .dish-text .mini-rule{width:26px;height:1px;background:var(--tan);margin:8px auto}
  .dish-text p{font-size:10px;line-height:14px;color:var(--muted)}
</style>
</head>
<body>

<header class="site-header">
  <div class="brand-badge">
    <svg width="294" height="136" viewBox="0 0 294 136">
      <path d="M0 0 H294 V70 L147 126 L0 70 Z" fill="#ffffff"/>
      <path d="M2 80 L147 134 L292 80" fill="none" stroke="#a88c67" stroke-width="4"/>
    </svg>
    <span class="brand-dot"></span>
    <div class="brand-name">TEATRO LUCERNA</div>
    <div class="brand-tag">Ristorante Italiano</div>
  </div>

  <nav class="main-nav">
    <a class="is-active" href="#">HOME</a>
    <a href="#">MENU</a>
    <a href="#">GROUP MENU</a>
    <a href="#">RESERVATION</a>
    <a href="#">CONTACT</a>
  </nav>

  <div class="contact-block">
    <div class="contact-hours">
      <svg width="9" height="9" viewBox="0 0 10 10"><circle cx="5" cy="5" r="4.2" fill="none" stroke="#6f6f6f" stroke-width="1"/><path d="M5 2.5V5H7" fill="none" stroke="#6f6f6f" stroke-width="1"/></svg>
      18:00 - 23:00
    </div>
    <div class="contact-phone">(+31) 20 555 0148</div>
  </div>
</header>

<section class="hero" role="img" aria-label="Photo of the warmly lit restaurant dining room with set tables and a ring of bulb lights">
  <div class="hero-content">
    <div class="hero-rule"></div>
    <div class="hero-script">Welcome to</div>
    <h1 class="hero-title">TEATRO LUCERNA</h1>
    <p class="hero-lead">The Italian restaurant located in the heart of Amsterdam</p>
    <div class="hero-rule bottom"></div>
  </div>
</section>

<section class="reserve-bar">
  <div class="reserve-heading"><strong>RESERVE</strong><span>YOUR TABLE</span></div>
  <svg class="reserve-divider" width="14" height="71" viewBox="0 0 14 71"><path d="M2 0 V28 L10 36 L2 44 V71" fill="none" stroke="#ffffff" stroke-width="1.5"/></svg>
  <span class="field-label" style="left:347px">Guests</span>
  <div class="field" style="left:417px;width:160px">no. of guests
    <svg width="16" height="12" viewBox="0 0 16 12"><circle cx="5" cy="3" r="2.6" fill="#ffffff"/><circle cx="11" cy="3.5" r="2.2" fill="#ffffff"/><path d="M0 12 C0 7 10 7 10 12Z M8 12 C8 8 16 8 16 12Z" fill="#ffffff"/></svg>
  </div>
  <span class="field-label" style="left:606px">When</span>
  <div class="field" style="left:663px;width:231px">select date
    <svg width="12" height="12" viewBox="0 0 12 12"><rect x="0.5" y="1.5" width="11" height="10" fill="none" stroke="#ffffff"/><path d="M0.5 4.5H11.5M3 0V3M9 0V3" stroke="#ffffff"/></svg>
  </div>
  <div class="reserve-btn">RESERVE</div>
</section>

<section class="specials">
  <h2 class="specials-title">MONTHLY SPECIAL</h2>
  <div class="specials-rule"></div>
  <div class="dish-row">
    <article class="dish">
      <div class="dish-photo" role="img" aria-label="Photo of a pasta dish"></div>
      <div class="dish-text"><h3>LOREM IPSUM</h3><div class="mini-rule"></div><p>Fresh pasta with seasonal herbs</p></div>
    </article>
    <article class="dish">
      <div class="dish-photo" role="img" aria-label="Photo of a grilled seafood plate"></div>
      <div class="dish-text"><h3>LOREM IPSUM</h3><div class="mini-rule"></div><p>Grilled fish with lemon butter</p></div>
    </article>
    <article class="dish">
      <div class="dish-photo" role="img" aria-label="Photo of a fresh salad"></div>
      <div class="dish-text"><h3>LOREM IPSUM</h3><div class="mini-rule"></div><p>Garden salad with aged balsamic</p></div>
    </article>
    <article class="dish">
      <div class="dish-photo" role="img" aria-label="Photo of spaghetti with tomato sauce"></div>
      <div class="dish-text"><h3>LOREM IPSUM</h3><div class="mini-rule"></div><p>Spaghetti with slow tomato sauce</p></div>
    </article>
  </div>
</section>

</body>
</html>
```